Suds Haven Laundromat Wordpress Design

We need a Wordpress website design for our laundromat, Suds Haven Atlanta, at www.sudshavenatlanta-example.com. We would like to have 6 pages: Home, About Us, Services, Locations, Reviews and Contact us. We will provide content for the text on each page. What we do: We are a full service laundromat that provides dry cleaning drop off, professional laundry services, wash dry fold and self service laundry to the local community. We would like to use the color scheme from our logo to convey a warm, safe, and bright business that caters to its diverse community.
Updates

I like the structure of this laundromat website: http://www.washtroveusa-example.com/ Using my logo and color scheme in the above referenced website is what. Am looking for. The photos attached to the project with the female model should be used as a primary focus and supplemented by actual photos of the equipment.

Target Market(s)

Our target market is a diverse group of people from Midtown Atlanta - LGBTQ community /Locals/Regulars that have been coming to laundromat for 30 years.

Industry/Entity Type

Laundromat

Coding

Coded - Design and coding required

Number of Pages Required

5+ page

Font styles to use
Sans Serif

Colors
0054AA
0677BA
7BADD7
CADEEF
E8F1F8

Requirements
Must have
• Feature this video on the main page: https://videohost-example.com/xq7Rm2bPz4k

```html
<!DOCTYPE html>
<html lang="en">
<head>
<meta charset="utf-8">
<title>Suds Haven Laundromat</title>
<link href="https://fonts.googleapis.com/css2?family=Bebas+Neue&family=Poppins:wght@400;500&display=swap" rel="stylesheet">
<style>
:root{
  --blue-deep:#0054aa;
  --blue:#0677ba;
  --blue-bright:#0a9be0;
  --blue-soft:#7badd7;
  --blue-pale:#cadeef;
  --tint:#f1f5f9;
  --ink:#2b2b2b;
  --body:#444;
  --footer:#2e4a6f;
  --white:#fff;
}
*{box-sizing:border-box;margin:0;padding:0}
html,body{width:1200px;height:2940px;overflow:hidden;background:var(--white)}
body{position:relative;font-family:"Poppins",sans-serif;color:var(--body)}
.abs{position:absolute}
.heading{font-family:"Bebas Neue",sans-serif;font-weight:400;color:var(--ink);letter-spacing:.5px}
.heading span{color:var(--blue)}
.btn{position:absolute;background:var(--blue-bright);color:var(--white);font-size:13px;font-weight:500;display:flex;align-items:center;justify-content:center;border-radius:2px}

/* header */
.site-header{top:0;left:0;width:1200px;height:90px;background:var(--white)}
.brand{left:161px;top:30px;font-size:27px;color:var(--blue-deep);font-family:"Bebas Neue",sans-serif;display:flex;align-items:center;gap:8px}
.brand i{display:block;width:14px;height:14px;border-radius:50%;background:var(--blue-bright)}
.main-nav a{position:absolute;top:38px;font-size:15px;color:#333;text-decoration:none}

/* hero */
.hero{top:90px;left:0;width:1200px;height:637px;background:linear-gradient(180deg,#b9c6c6 0%,#9fa9a6 45%,#8e8f86 100%)}
.hero-title{position:absolute;top:290px;left:0;width:1200px;text-align:center;font-family:"Bebas Neue",sans-serif;font-size:47px;line-height:48px;color:var(--white);text-shadow:0 2px 6px rgba(0,0,0,.5)}

/* about */
.about-photo{left:189px;top:874px;width:308px;height:308px;border-radius:50%;background:radial-gradient(circle at 50% 40%,#b9a68e,#7d7468)}
.section-rule{position:absolute;height:3px;width:46px;background:var(--blue-bright)}
.about-text{left:573px;top:893px;width:468px;font-size:14px;line-height:27px;color:#333}
.about-text p+p{margin-top:5px}

/* services */
.services{top:1280px;left:0;width:1200px;height:596px;background:var(--tint)}
.service h3{font-family:"Bebas Neue",sans-serif;font-weight:400;font-size:21px;color:var(--blue);margin:16px 0 4px}
.service p{font-size:11.5px;line-height:19px;color:#444}
.service p b{color:var(--blue-bright);font-weight:400}
.service{position:absolute;width:250px}
.service svg{display:block}
.services-photo{left:715px;top:1442px;width:324px;height:324px;border-radius:50%;background:radial-gradient(circle at 45% 55%,#8e8c86,#c9c8c4 60%,#e2e2df)}

/* testimonials */
.card{position:absolute;top:2081px;width:277px;height:204px;background:var(--white);box-shadow:0 12px 18px -8px rgba(0,0,0,.15);text-align:center}
.card .quote{position:absolute;left:95px;top:-43px;width:86px;height:86px;border-radius:50%;background:#dcdcdc;border:4px solid #f4f4f4;display:flex;align-items:center;justify-content:center;color:#9a9a9a;font-family:"Bebas Neue",sans-serif;font-size:54px;line-height:1;padding-top:18px}
.card.active .quote{background:var(--blue);color:var(--white);border-color:#e9f1f8}
.card h4{margin-top:62px;font-size:17px;font-weight:500;color:var(--blue)}
.card p{margin:8px 16px 0;font-size:11.5px;line-height:23px;color:#444}
.card .more{position:absolute;left:118px;bottom:-20px;width:40px;height:40px;border-radius:50%;background:var(--blue);clip-path:inset(0 0 50% 0);color:var(--white);font-size:15px;line-height:24px;font-weight:500}
.dots{top:2326px;left:563px;display:flex;gap:8px}
.dots i{display:block;width:12px;height:12px;border-radius:50%;border:1.5px solid var(--blue)}
.dots i.on{background:var(--blue)}

/* footer */
.site-footer{top:2414px;left:0;width:1200px;height:526px;background:var(--footer);color:var(--white)}
.footer-brand{top:2497px;left:0;width:1200px;text-align:center;font-family:"Bebas Neue",sans-serif;font-size:52px;color:var(--white)}
.rule{position:absolute;height:1px;background:rgba(255,255,255,.18)}
.footer-nav a{position:absolute;top:2645px;font-size:15.5px;color:var(--white);text-decoration:none}
.social{position:absolute;top:2641px;width:30px;height:30px;border-radius:50%;background:var(--white)}
.info{font-size:14px;line-height:24px;color:var(--white)}
.info .note{color:#1ea8ea}
.copyright{top:2876px;left:0;width:1200px;text-align:center;font-size:12.5px;color:var(--white)}
.copyright b{font-weight:500}
</style>
</head>
<body>

<header class="abs site-header">
  <div class="abs brand"><i></i>Suds Haven</div>
  <nav class="main-nav">
    <a style="left:537px;font-weight:500">Home</a>
    <a style="left:606px">About Us</a>
    <a style="left:697px">Services</a>
    <a style="left:783px">Locations</a>
    <a style="left:876px">Reviews</a>
    <a style="left:963px">Contact Us</a>
  </nav>
</header>

<section class="abs hero" role="img" aria-label="Photo of a woman in a blue dress walking through a retro laundromat lined with front-loading washers">
  <svg class="abs" style="left:270px;top:170px" width="320" height="330" viewBox="0 0 320 330" aria-hidden="true">
    <path d="M200 24 A150 150 0 1 0 240 300" fill="none" stroke="var(--blue)" stroke-width="5"/>
  </svg>
  <h1 class="hero-title">WE PROVIDE FAST, FRIENDLY &amp; PROFESSIONAL<br>DRY CLEANING &amp; LAUNDRY SERVICE<br>IN MIDTOWN ATLANTA, USA</h1>
  <a class="btn" style="left:543px;top:448px;width:113px;height:41px">Visit Us</a>
</section>

<section class="about">
  <svg class="abs" style="left:168px;top:790px" width="350" height="415" viewBox="0 0 350 415" aria-hidden="true">
    <path d="M240 70 A178 178 0 1 0 280 360" fill="none" stroke="var(--blue-deep)" stroke-width="6"/>
    <circle cx="220" cy="16" r="9" fill="none" stroke="var(--blue-deep)" stroke-width="4"/>
    <circle cx="158" cy="46" r="5" fill="none" stroke="var(--blue-deep)" stroke-width="3"/>
    <circle cx="271" cy="42" r="5" fill="none" stroke="var(--blue-deep)" stroke-width="3"/>
  </svg>
  <div class="abs about-photo" role="img" aria-label="Photo of a woman in a knit cap listening to music with earphones"></div>
  <svg class="abs" style="left:414px;top:1073px" width="86" height="86" viewBox="0 0 86 86" aria-label="Play video" role="img">
    <circle cx="43" cy="43" r="42" fill="var(--white)"/>
    <circle cx="43" cy="43" r="34" fill="var(--blue-soft)"/>
    <circle cx="43" cy="43" r="25" fill="var(--white)"/>
    <path d="M37 32 L54 43 L37 54 Z" fill="var(--blue-deep)"/>
  </svg>
  <h2 class="abs heading" style="left:573px;top:832px;font-size:36px">ABOUT <span>US</span></h2>
  <div class="section-rule" style="left:573px;top:875px"></div>
  <div class="abs about-text">
    <p>Suds Haven is family-owned laundromat that has been serving Midtown, GA for over 45 years. We are proud to offer high quality and convenient services to the area residents and business owners and strive to keep our customers clothing in tip top shape.</p>
    <p>Whether you have commercial laundry needs, are washing clothes for your family, or want to relax that weekend and have us pick up and wash/dry/fold for you, the professionals at Suds Haven are ready to meet your goals.</p>
  </div>
  <a class="btn" style="left:572px;top:1125px;width:150px;height:40px">Contact Us Today</a>
</section>

<section class="abs services"></section>
<h2 class="abs heading" style="left:162px;top:1356px;font-size:36px">OUR <span>SERVICES</span></h2>
<div class="section-rule" style="left:162px;top:1399px"></div>

<div class="service" style="left:160px;top:1441px">
  <svg width="62" height="62" viewBox="0 0 62 62" fill="none" stroke="var(--blue)" stroke-width="2"><path d="M8 60 V26 L22 14 H40 L54 26 V60 M22 14 L31 28 L40 14 M31 28 V60 M38 42 h10 v10 h-10z"/><path d="M4 6 v6 M1 9 h6 M58 6 v6 M55 9 h6" stroke="var(--blue-bright)"/></svg>
  <h3>WASH DRY FOLD</h3>
  <p>Tired, too much to do, own a business and need linens, sheets, towels, etc., cleaned? Don't worry, we can do your laundry...<b>[+]</b></p>
</div>
<div class="service" style="left:435px;top:1441px">
  <svg width="62" height="62" viewBox="0 0 62 62" fill="none" stroke="var(--blue)" stroke-width="2"><rect x="2" y="24" width="30" height="36"/><line x1="2" y1="32" x2="32" y2="32"/><circle cx="17" cy="46" r="8"/><path d="M36 38 h24 M40 38 l16 22 M56 38 l-16 22"/><path d="M16 16 l10 -8 l10 8 M34 14 l10 -8 l10 8" stroke="var(--blue-bright)"/></svg>
  <h3>PROFESSIONAL LAUNDRY SERVICES</h3>
  <p>Lorem ipsum dolor sit amet, consectetuer adipiscing elit, sed diam nonummy nibhfrt euismod tincidunt ut laoreet dolore...[+]</p>
</div>
<div class="service" style="left:160px;top:1644px">
  <svg width="62" height="62" viewBox="0 0 62 62" fill="none" stroke="var(--blue)" stroke-width="2"><rect x="6" y="2" width="46" height="58" rx="2"/><line x1="6" y1="14" x2="52" y2="14"/><circle cx="29" cy="37" r="13"/><path d="M36 40 h24 M36 46 h24 M36 52 h24 M36 58 h24"/><path d="M4 34 v6 M1 37 h6" stroke="var(--blue-bright)"/></svg>
  <h3>DRY CLEANING DROP OFF</h3>
  <p>Do you have clothing or linens that are made from delicate fabrics that aren't machine washable?...<b>[+]</b></p>
</div>
<div class="service" style="left:435px;top:1644px">
  <svg width="62" height="62" viewBox="0 0 62 62" fill="none" stroke="var(--blue)" stroke-width="2"><circle cx="46" cy="10" r="7"/><path d="M34 60 V30 Q46 20 58 30 V60"/><path d="M2 60 V30 L12 22 H24 L30 30 V60 M12 22 L18 32 L24 22 M18 32 V60" stroke="var(--blue-bright)"/></svg>
  <h3>SELF SERVICE LAUNDRY</h3>
  <p>With over 40 well maintained self-service washers and dryers laundry will be a thing of the past!...<b>[+]</b></p>
</div>

<svg class="abs" style="left:708px;top:1388px" width="340" height="392" viewBox="0 0 340 392" aria-hidden="true">
  <path d="M30 130 A165 165 0 1 1 180 376" fill="none" stroke="var(--blue-deep)" stroke-width="6"/>
  <circle cx="133" cy="15" r="9" fill="none" stroke="var(--blue-deep)" stroke-width="4"/>
  <circle cx="88" cy="41" r="5" fill="none" stroke="var(--blue-deep)" stroke-width="3"/>
  <circle cx="188" cy="42" r="5" fill="none" stroke="var(--blue-deep)" stroke-width="3"/>
</svg>
<div class="abs services-photo" role="img" aria-label="Photo of stainless steel front-loading washing machines"></div>

<h2 class="abs heading" style="left:0;width:1200px;text-align:center;top:1950px;font-size:36px">CUSTOMER <span>TESTIMONIALS</span></h2>
<div class="section-rule" style="left:577px;top:1998px;width:62px"></div>

<article class="card" style="left:161px">
  <div class="quote">99</div>
  <h4>Marcus Dale</h4>
  <p>Great drop off laundry location to have professionals do your laundry. They are quick, honor requests about how to bag it up, and are friendly and reasonable.</p>
  <div class="more">+</div>
</article>
<article class="card active" style="left:461px">
  <div class="quote">99</div>
  <h4>Jordan Reyes</h4>
  <p>Great customer service, friendly staff, the place looks clean &amp; they have the option to pay with your phone &amp; coins, great acco-mmodating to the customers. Thank you!</p>
  <div class="more">+</div>
</article>
<article class="card" style="left:762px">
  <div class="quote">99</div>
  <h4>Isaac Warren</h4>
  <p>This is one of the cleanest and friendly Coin Laundromats I've ever been too. Great place!</p>
  <div class="more">+</div>
</article>
<div class="abs dots"><i></i><i></i><i class="on"></i><i></i></div>

<footer class="abs site-footer"></footer>
<div class="abs footer-brand">SUDS HAVEN</div>
<div class="rule" style="left:320px;top:2614px;width:560px"></div>
<nav class="footer-nav">
  <a style="left:254px">Home</a>
  <a style="left:338px">About Us</a>
  <a style="left:446px">Services</a>
  <a style="left:549px">Locations</a>
  <a style="left:659px">Reviews</a>
  <a style="left:762px">Contact Us</a>
</nav>
<span class="social" style="left:879px" aria-label="Social link"></span>
<span class="social" style="left:924px" aria-label="Social link"></span>

<svg class="abs" style="left:246px;top:2722px" width="18" height="80" viewBox="0 0 18 80" fill="none" stroke="var(--white)" stroke-width="1.3" aria-hidden="true">
  <circle cx="9" cy="9" r="8"/><path d="M1 9 h16 M9 1 q-5 8 0 16 q5 -8 0 -16"/>
  <path d="M3 62 q2 -3 4 0 l-1 3 q2 5 6 7 l3 -1 q3 2 0 4 q-5 2 -10 -4 q-5 -6 -2 -9z"/>
</svg>
<div class="abs info" style="left:276px;top:2722px;width:330px">Brookhaven Plaza, 2210 Elmwood Ave NE., # 118, Atlanta, GA 30324</div>
<div class="abs info" style="left:276px;top:2776px">(404) 555-0142</div>
<div class="abs info" style="left:611px;top:2722px;width:380px"><span class="note">Delivery Available* please contact us for details</span><br><span style="display:block;margin-top:8px">Covid 19 hours - open 7 days a week 8 am to 8 pm<br>Last wash begins 6:30 pm</span></div>
<div class="rule" style="left:161px;top:2832px;width:878px"></div>
<div class="abs copyright">Copyright © 2021 <b>Suds Haven Atlanta</b>. All Rights Reserved.</div>

</body>
</html>
```